Business card for law firm

Need business card for new law firm. Think confident, authoritative, conservative, but not stuffy or old-fashioned.

Contact Information for Business Card

Content for card - logo (uploaded), plus the following:

Paul Whitcombe (larger font)
Managing Partner (larger font, but not as large as name)
Level 9, 7 Ferris Lane
Sydney NSW 2000
Main Tel 02 9364 2710
Direct Tel 02 8472 3159
Email paul@qvlegal.com.au
www.qvlegal.com.au

Letterhead design should include logo plus:
Level 9, 7 Ferris Lane
Sydney NSW 2000
Tel 02 8472 3159
www.qvlegal.com.au

```html
<!DOCTYPE html>
<html lang="en">
<head>
<meta charset="utf-8">
<title>Quayvale Lawyers – Business Card</title>
<link href="https://fonts.googleapis.com/css2?family=Cinzel:wght@400&family=Open+Sans:wght@400&display=swap" rel="stylesheet">
<style>
  :root {
    --navy: #0b1f5c;
    --ink: #111111;
    --paper: #ffffff;
    --backdrop: #6a6a6a;
  }
  * { margin: 0; padding: 0; box-sizing: border-box; }
  html, body {
    width: 1200px; height: 802px; overflow: hidden;
    background: var(--backdrop);
  }
  .stage { position: relative; width: 1200px; height: 802px; }
  .card {
    position: absolute; top: 274px;
    width: 442px; height: 265px;
    background: var(--paper);
    box-shadow: 0 3px 8px rgba(0,0,0,0.45);
    overflow: hidden;
  }
  .card--front { left: 136px; }
  .card--back { left: 624px; }

  .accent-panel {
    position: absolute; left: 0; top: 0;
    width: 193px; height: 265px;
    background: var(--navy);
  }

  .wordmark {
    position: absolute; text-align: center;
    font-family: "Cinzel", serif; font-weight: 400; color: var(--ink);
  }
  .wordmark__name { display: block; line-height: 1; }
  .wordmark__type { display: block; line-height: 1; }
  .card--front .wordmark { left: 222px; top: 44px; width: 200px; }
  .card--front .wordmark__name { font-size: 27px; letter-spacing: 0.5px; }
  .card--front .wordmark__type { font-size: 10px; letter-spacing: 9px; margin-top: 6px; padding-left: 9px; }
  .card--back .wordmark { left: 0; top: 152px; width: 442px; }
  .card--back .wordmark__name { font-size: 32px; letter-spacing: 0.5px; }
  .card--back .wordmark__type { font-size: 12px; letter-spacing: 12px; margin-top: 7px; padding-left: 12px; }

  .person { position: absolute; left: 222px; top: 106px; }
  .person__name {
    font-family: "Cinzel", serif; font-size: 17px; color: var(--navy);
    line-height: 1.1; letter-spacing: 0.2px;
  }
  .person__role {
    font-family: "Open Sans", sans-serif; font-size: 12.5px; color: var(--ink); line-height: 1.2;
  }

  .contact {
    position: absolute; left: 222px; top: 143px;
    list-style: none;
    font-family: "Open Sans", sans-serif; font-size: 12.5px; color: var(--ink);
  }
  .contact__item { display: flex; align-items: center; height: 16px; }
  .contact__icon { width: 10px; height: 10px; margin-right: 3px; fill: var(--ink); }
  .contact__note { font-size: 11px; margin-left: 3px; }

  .address {
    position: absolute; left: 222px; top: 216px;
    font-family: "Open Sans", sans-serif; font-size: 12.5px; color: var(--ink);
    font-style: normal; line-height: 15.5px;
  }
</style>
</head>
<body>
<main class="stage">
  <section class="card card--front" aria-label="Business card front">
    <div class="accent-panel"></div>
    <div class="wordmark">
      <span class="wordmark__name">QUAYVALE</span>
      <span class="wordmark__type">LAWYERS</span>
    </div>
    <div class="person">
      <p class="person__name">PAUL WHITCOMBE</p>
      <p class="person__role">Managing Partner</p>
    </div>
    <ul class="contact">
      <li class="contact__item">
        <svg class="contact__icon" viewBox="0 0 10 10" aria-hidden="true"><path d="M1 3.2C1 2 2.5 1.3 5 1.3S9 2 9 3.2v.8H7V3.2H3V4H1z"/><path d="M2.2 4.6h5.6L9 8.7H1z"/></svg>
        02 9364 2710
      </li>
      <li class="contact__item">
        <svg class="contact__icon" viewBox="0 0 10 10" aria-hidden="true"><path d="M1 3.2C1 2 2.5 1.3 5 1.3S9 2 9 3.2v.8H7V3.2H3V4H1z"/><path d="M2.2 4.6h5.6L9 8.7H1z"/></svg>
        02 8472 3159<span class="contact__note">(DIRECT)</span>
      </li>
      <li class="contact__item">
        <svg class="contact__icon" viewBox="0 0 10 10" aria-hidden="true"><path d="M1 2.5h8v5H1z"/><path d="M1.5 3l3.5 2.6L8.5 3" fill="none" stroke="#fff" stroke-width="0.8"/></svg>
        paul@qvlegal.com.au
      </li>
      <li class="contact__item">
        <svg class="contact__icon" viewBox="0 0 10 10" aria-hidden="true"><circle cx="5" cy="5" r="4.2"/><path d="M3 3.5c1 .3 1.5 1 1 2s.5 1.5 1 2.5M6.5 2c-.3 1 .5 1.5 1.5 1.8" fill="none" stroke="#fff" stroke-width="0.8"/></svg>
        www.qvlegal.com.au
      </li>
    </ul>
    <address class="address">
      Level 9, 7 Ferris Lane<br>
      Sydney NSW 2000
    </address>
  </section>

  <section class="card card--back" aria-label="Business card back">
    <div class="wordmark">
      <span class="wordmark__name">QUAYVALE</span>
      <span class="wordmark__type">LAWYERS</span>
    </div>
  </section>
</main>
</body>
</html>
```